Summer Music/Chorus/Choir Camp for Young Singers Ages 8-13

We need a flyer for a summer camp for young singers ages 8-13. We are nonprofit community children's chorus in Miami, FL. Our camp provides specialized training in music theory, sight-reading,and aural training through daily choral rehearsals in an environment that is both positive and a lot of fun! Our camp offers children the opportunity to come as they are, no matter the level of experience, and grow tremendously in their musicianship skills. In addition to this, our campers participate in song-writing, masterclasses, community performances, and media projects. The final design should be clean, fun, not too crowded, should appeal to boys and girls ages 8-13, and something someone that age would consider "cool" and not too childish. Drawings are cool, something different.
Updates

Target Market(s)

Ages 8-13 and parents of those kids.

Industry/Entity Type

Community

Requirements
Must have
• All info attached.
Nice to have
• Things that relate to music, especially related to singing/choirs
Should not have
• instruments, stock photos of children, or photos from our website (unless they are used very creatively), or photos in general. I've attached our previous camp flyer and our current organization flyer but I don't necessarily want this flyer to look like those.

```html
<!DOCTYPE html>
<html lang="en">
<head>
<meta charset="utf-8">
<title>Summer Camp – The Young Harmony Chorus</title>
<link href="https://fonts.googleapis.com/css2?family=Fredoka:wght@600;700&family=Roboto+Slab:wght@700&family=Tinos:wght@400;700&display=swap" rel="stylesheet">
<style>
  :root {
    --sun-core: #fff7b8;
    --sun-mid: #ffd21f;
    --sun-edge: #f7a712;
    --title-white: #ffffff;
    --title-navy: #1f4d6b;
    --camp-red: #e8402a;
    --body-red: #e2452b;
    --band-red: #dc3a2a;
    --band-deep: #c22a24;
    --band-orange: #f46a2a;
    --teal: #1f6f8f;
    --cream: #fff6ea;
    --white: #ffffff;
    --logo-green: #2f7d4f;
  }
  * { margin: 0; padding: 0; box-sizing: border-box; }
  html, body { width: 927px; height: 1200px; overflow: hidden; }
  body { background: #ffffff; font-family: "Tinos", "Times New Roman", serif; }

  .flyer {
    position: relative;
    width: 927px;
    height: 1200px;
    overflow: hidden;
    background: radial-gradient(circle at 50% 22%, var(--sun-core) 0%, var(--sun-mid) 38%, var(--sun-edge) 100%);
  }

  .kids-illustration {
    position: absolute;
    left: 220px; top: 15px;
    width: 485px; height: 200px;
    border-radius: 90px 90px 20px 20px;
    background: linear-gradient(180deg, #ffe27a 0%, #f6b24a 55%, #2e8a3c 100%);
    opacity: .85;
  }

  .title {
    position: absolute;
    left: 0; width: 100%;
    text-align: center;
    font-family: "Fredoka", "Arial Rounded MT Bold", sans-serif;
    font-weight: 700;
  }
  .title-summer {
    top: 188px;
    font-size: 178px;
    line-height: 1;
    letter-spacing: -2px;
    color: var(--title-white);
    -webkit-text-stroke: 9px var(--title-navy);
    paint-order: stroke fill;
  }
  .title-camp {
    top: 342px;
    left: 52px;
    font-size: 92px;
    line-height: 1;
    color: var(--camp-red);
    -webkit-text-stroke: 6px var(--white);
    paint-order: stroke fill;
  }

  .intro {
    position: absolute;
    left: 58px; top: 448px;
    width: 811px;
    text-align: center;
    font-size: 18px;
    line-height: 24.5px;
    color: var(--body-red);
  }

  .bands { position: absolute; left: 0; top: 0; }

  .circle {
    position: absolute;
    border-radius: 50%;
    text-align: center;
    font-family: "Tinos", "Times New Roman", serif;
  }
  .circle h2 {
    font-family: "Roboto Slab", "Rockwell", serif;
    font-weight: 700;
  }
  .location {
    left: 376px; top: 629px;
    width: 288px; height: 288px;
    background: var(--teal);
    color: var(--white);
    padding-top: 56px;
  }
  .location h2 { font-size: 32px; margin-bottom: 6px; }
  .location p { font-size: 17px; font-weight: 700; line-height: 25px; }

  .cost {
    left: 636px; top: 578px;
    width: 270px; height: 270px;
    background: var(--camp-red);
    color: var(--white);
    border: 5px solid var(--white);
    padding-top: 62px;
  }
  .cost h2 { font-size: 33px; line-height: 1.1; }
  .cost .cost-session { font-size: 20px; font-weight: 700; margin-top: 2px; }
  .cost .cost-note { font-size: 14px; font-weight: 700; margin-top: 8px; }

  .dates {
    left: 496px; top: 815px;
    width: 340px; height: 340px;
    background: var(--white);
    color: var(--camp-red);
    padding-top: 86px;
  }
  .dates h2 { font-size: 26px; line-height: 33px; }
  .dates .dates-extended { font-size: 16px; font-weight: 700; line-height: 22px; margin-top: 16px; }

  .contact {
    position: absolute;
    left: 43px; top: 822px;
    color: var(--white);
  }
  .contact h2 {
    font-family: "Roboto Slab", "Rockwell", serif;
    font-size: 23px;
    font-weight: 700;
    margin-bottom: 10px;
  }
  .contact p { font-size: 17px; font-weight: 700; line-height: 28px; }

  .org-mark {
    position: absolute;
    left: 42px; top: 920px;
    width: 228px; height: 118px;
    background: var(--white);
    display: flex;
    align-items: center;
    gap: 12px;
    padding: 0 16px;
  }
  .org-mark .dot {
    width: 20px; height: 20px; border-radius: 50%;
    background: var(--logo-green); flex: none;
  }
  .org-mark span {
    font-size: 22px; font-weight: 700; line-height: 26px;
    color: var(--logo-green);
  }

  .partner {
    position: absolute;
    top: 1060px; height: 48px;
    background: var(--white);
  }
  .partner-a { left: 42px; width: 66px; }
  .partner-b { left: 121px; width: 134px; }
  .partner-c { left: 265px; width: 164px; top: 1072px; height: 34px; }

  .footer-note {
    position: absolute;
    left: 0; top: 1163px; width: 100%;
    text-align: center;
    font-size: 16px;
    font-weight: 700;
    color: var(--cream);
  }
</style>
</head>
<body>
<main class="flyer">
  <div class="kids-illustration" role="img" aria-label="Cartoon of three smiling children peeking over the title, the middle one holding a microphone"></div>

  <h1>
    <span class="title title-summer">Summer</span>
    <span class="title title-camp">Camp</span>
  </h1>

  <p class="intro">"Youth and children who love to sing will have a blast at our choral camp! Our music educators and industry professionals are dedicated to enhancing the lives of young singers through choral training which develops vocal technique, ear-training, music reading, and interpersonal skills. Activities are fun and interactive and former music training is not necessary. Singers in grades 3-9 are invited to attend! Register today!</p>

  <svg class="bands" width="927" height="1200" viewBox="0 0 927 1200" aria-hidden="true">
    <defs>
      <linearGradient id="bandRed" x1="0" y1="0" x2="1" y2="1">
        <stop offset="0" stop-color="#e8442c"/>
        <stop offset="1" stop-color="#c22a24"/>
      </linearGradient>
    </defs>
    <path d="M0 790 C 180 770, 340 800, 470 860 C 620 930, 760 960, 927 900 L 927 1200 L 0 1200 Z" fill="url(#bandRed)"/>
    <circle cx="905" cy="1090" r="170" fill="#f6a31e"/>
    <path d="M0 1140 C 300 1120, 600 1130, 927 1150 L 927 1200 L 0 1200 Z" fill="#c9302a"/>
  </svg>

  <section class="circle location">
    <h2>Location</h2>
    <p>Southpoint Cultural<br>Arts Center,<br>4820 Palm Grove<br>Avenue Miami, FL 33100.</p>
  </section>

  <section class="circle cost">
    <h2>Cost : $300</h2>
    <p class="cost-session">for 2-week session</p>
    <p class="cost-note">Price does not include lunch.</p>
  </section>

  <section class="circle dates">
    <h2>Dates &amp; Times<br>July 18-29<br>9am-3pm (M-F)</h2>
    <p class="dates-extended">Extended hours available<br>(7:30am-5:30pm) for an extra<br>$50 per week.</p>
  </section>

  <section class="contact">
    <h2>Our Contact information</h2>
    <p>Phone- 555.014.2290</p>
    <p>Email- info@youngharmonychorus.org</p>
  </section>

  <div class="org-mark">
    <span class="dot"></span>
    <span>The Young Harmony Chorus</span>
  </div>

  <div class="partner partner-a" role="img" aria-label="Partner badge"></div>
  <div class="partner partner-b" role="img" aria-label="Partner badge"></div>
  <div class="partner partner-c" role="img" aria-label="Partner badge"></div>

  <p class="footer-note">"The Young Harmony Chorus is a 501 (c)(3) Nonprofit organization. Donations made to YHC are tax-exempt."</p>
</main>
</body>
</html>
```